SaaS Early tech startup business card design

Unique design for experience ecommerce platform company. the business cards will be used by executive members. conformance with color code is required.

```html
<!DOCTYPE html>
<html lang="en">
<head>
<meta charset="utf-8">
<title>nuvo business card</title>
<link rel="stylesheet" href="https://fonts.googleapis.com/css2?family=Open+Sans:wght@400;600;700&display=swap">
<style>
  :root {
    --backdrop: #d6d6d6;
    --paper: #ffffff;
    --brand-blue: #17618f;
    --brand-teal: #1db394;
    --ink: #1e1e1e;
    --card-shadow: rgba(0, 0, 0, 0.18);
  }
  * { box-sizing: border-box; margin: 0; padding: 0; }
  html, body {
    width: 1200px;
    height: 815px;
    overflow: hidden;
    background: var(--backdrop);
    font-family: "Open Sans", Arial, sans-serif;
  }
  .canvas {
    width: 1200px;
    height: 815px;
    display: flex;
    align-items: center;
    justify-content: center;
    gap: 40px;
  }
  .card {
    position: relative;
    width: 540px;
    height: 310px;
    background: var(--paper);
    border-bottom: 4px solid var(--brand-teal);
    box-shadow: 0 10px 24px var(--card-shadow);
  }
  .wordmark {
    display: flex;
    align-items: center;
    gap: 10px;
    color: var(--brand-blue);
    font-weight: 700;
    letter-spacing: -1px;
    line-height: 1;
  }
  .wordmark-square {
    background: var(--brand-teal);
    flex: none;
  }

  /* front: contact side */
  .card-front .wordmark {
    position: absolute;
    left: 0;
    width: 270px;
    top: 0;
    height: 100%;
    justify-content: center;
    font-size: 56px;
  }
  .card-front .wordmark-square { width: 14px; height: 14px; }
  .divider {
    position: absolute;
    left: 283px;
    top: 70px;
    width: 1px;
    height: 168px;
    background: var(--brand-teal);
  }
  .contact {
    position: absolute;
    left: 306px;
    top: 66px;
    color: var(--ink);
    font-size: 11.5px;
    line-height: 1.35;
  }
  .contact-name {
    color: var(--brand-blue);
    font-size: 20px;
    font-weight: 700;
    line-height: 1.1;
  }
  .contact-role { margin-bottom: 14px; }
  .contact-address { margin-bottom: 14px; }
  .contact-line {
    display: flex;
    align-items: center;
    gap: 7px;
  }
  .contact-line svg { width: 10px; height: 10px; flex: none; }

  /* back: logo side */
  .card-back {
    display: flex;
    align-items: center;
    justify-content: center;
  }
  .card-back .wordmark { font-size: 104px; gap: 16px; }
  .card-back .wordmark-square { width: 24px; height: 24px; }
</style>
</head>
<body>
<main class="canvas">
  <section class="card card-front" aria-label="Business card, contact side">
    <div class="wordmark"><span>nuvo</span><span class="wordmark-square"></span></div>
    <div class="divider"></div>
    <div class="contact">
      <p class="contact-name">Daren Holt</p>
      <p class="contact-role">Managing Director</p>
      <p class="contact-address">Your location street here,<br>Country name, Country - 91542</p>
      <p class="contact-line">
        <svg viewBox="0 0 10 10" aria-hidden="true"><circle cx="5" cy="5" r="5" fill="var(--brand-blue)"/><path d="M3 2.6 4.2 3.8 3.7 4.5Q4.6 5.8 5.5 6.3L6.2 5.8 7.4 7 6.6 7.8Q4.3 7.2 2.2 3.4Z" fill="#fff"/></svg>
        +012 345 6789
      </p>
      <p class="contact-line">
        <svg viewBox="0 0 10 10" aria-hidden="true"><rect x="0.5" y="2" width="9" height="6.5" fill="var(--brand-blue)"/><path d="M0.8 2.4 5 5.8 9.2 2.4" fill="none" stroke="#fff" stroke-width="0.9"/></svg>
        info@youremail.com
      </p>
      <p class="contact-line">
        <svg viewBox="0 0 10 10" aria-hidden="true"><circle cx="5" cy="5" r="4.6" fill="var(--brand-blue)"/><path d="M0.6 5H9.4M5 0.5Q2.4 5 5 9.5M5 0.5Q7.6 5 5 9.5" fill="none" stroke="#fff" stroke-width="0.7"/></svg>
        www.yourwebsite.com
      </p>
    </div>
  </section>

  <section class="card card-back" aria-label="Business card, logo side">
    <div class="wordmark"><span>nuvo</span><span class="wordmark-square"></span></div>
  </section>
</main>
</body>
</html>
```